I need a design that promotes "A peak path hub for runners". services include assessment, massage, physiotherapy, pilates, suspension training, kinesiotaping in any combination.
I would like to bring the design into my website, flyers etc

Target Market(s)

athletes from beginner to elite - any age, male and female

Industry/Entity Type

Shop

Contact Information for Business Card

Peak-Path Hub for Runners
17 Corla Lane, Westmere, Kelmarsh
021 874 3061
tess.harlow@mailbrook.example

Logo Text

Logo styles of interest
Abstract Logo
Requirements
Nice to have
• Blue colour theme

```html
<!DOCTYPE html>
<html lang="en">
<head>
<meta charset="utf-8">
<title>Peak-Path Hub for Runners – Business Card</title>
<link rel="stylesheet" href="https://fonts.googleapis.com/css2?family=Oswald:wght@700&family=Lato:wght@400&family=Arimo:wght@400&display=swap">
<style>
  :root {
    --card-black: #000000;
    --brand-blue: #41bff8;
    --text-blue: #3fb8f2;
    --band-text: #ffffff;
  }
  html, body {
    margin: 0;
    padding: 0;
    overflow: hidden;
    background: var(--card-black);
  }
  .card {
    position: relative;
    width: 1200px;
    height: 693px;
    background: var(--card-black);
    overflow: hidden;
  }
  .top-rule {
    position: absolute;
    left: 0;
    top: 68px;
    width: 100%;
    height: 7px;
    background: var(--brand-blue);
  }
  .brand {
    position: absolute;
    left: 166px;
    top: 186px;
    display: flex;
    align-items: center;
    gap: 8px;
  }
  .brand-dot {
    width: 76px;
    height: 86px;
    border-radius: 50%;
    background: var(--brand-blue);
    flex: none;
  }
  .brand-name {
    margin: 0;
    font-family: "Oswald", "Arial Narrow", sans-serif;
    font-weight: 700;
    font-size: 64px;
    line-height: 1;
    letter-spacing: -1.5px;
    color: var(--brand-blue);
    white-space: nowrap;
    transform: translateY(12px);
  }
  .address {
    position: absolute;
    left: 500px;
    top: 338px;
    margin: 0;
    font-family: "Lato", "Calibri", sans-serif;
    font-style: normal;
    font-size: 35px;
    line-height: 57px;
    color: var(--text-blue);
  }
  .contact-band {
    position: absolute;
    left: 0;
    top: 561px;
    width: 100%;
    height: 80px;
    background: var(--brand-blue);
    display: flex;
    align-items: center;
    justify-content: space-between;
    padding: 0 54px 0 59px;
    box-sizing: border-box;
    font-family: "Arimo", "Arial", sans-serif;
    font-size: 38px;
    color: var(--band-text);
  }
  .contact-band span {
    white-space: nowrap;
  }
</style>
</head>
<body>
  <main class="card">
    <div class="top-rule"></div>

    <div class="brand">
      <div class="brand-dot"></div>
      <h1 class="brand-name">PEAK-PATH HUB FOR RUNNERS</h1>
    </div>

    <address class="address">
      17 Corla Lane,<br>
      Westmere,<br>
      Kelmarsh,
    </address>

    <footer class="contact-band">
      <span class="phone">Phone 021 874 3061</span>
      <span class="email">tess.harlow@mailbrook.example</span>
    </footer>
  </main>
</body>
</html>
```